Business Card Design

We are a commercial real estate brokerage in San Francisco, leasing office buildings downtown.
I would like a clean, elegant look. Simple but powerful .

Industry/Entity Type

Business

Contact Information for Business Card

Derek Holloway
lic# 07258143
415.555.0172
derek@velt-commercial.example
velt-commercial.example

```html
<!DOCTYPE html>
<html lang="en">
<head>
<meta charset="utf-8">
<title>Velt Commercial — Business Card</title>
<link rel="stylesheet" href="https://fonts.googleapis.com/css2?family=Open+Sans:wght@400;600&display=swap">
<style>
  :root {
    --backdrop: #4a3f39;
    --card: #0f0f11;
    --card-edge: #1c1c20;
    --steel: #8d9bb3;
    --steel-bright: #a9b7cf;
    --text-grey: #8b9099;
    --icon-grey: #9aa0aa;
    --rule: #3a3d44;
  }
  * { margin: 0; padding: 0; box-sizing: border-box; }
  html, body { width: 1200px; height: 768px; overflow: hidden; }
  body {
    background: var(--backdrop);
    position: relative;
    font-family: "Open Sans", sans-serif;
  }
  .card {
    position: absolute;
    top: 234px;
    width: 520px;
    height: 300px;
    background: var(--card);
    border: 1px solid var(--card-edge);
    box-shadow: 0 10px 24px rgba(0,0,0,0.45);
    overflow: hidden;
  }
  .card--front { left: 50px; }
  .card--back { left: 630px; }

  .company-name {
    font-family: "Open Sans", sans-serif;
    font-weight: 600;
    color: var(--steel);
    white-space: nowrap;
    line-height: 1.2;
  }

  .card--front .company-name {
    position: absolute;
    left: 0; right: 0; top: 126px;
    text-align: center;
    font-size: 34px;
  }

  .back-frame { position: absolute; left: 0; top: 0; }

  .contact {
    position: absolute;
    right: 210px;
    top: 70px;
    text-align: right;
  }
  .contact__name {
    font-weight: 600;
    font-size: 17px;
    color: var(--steel-bright);
  }
  .contact__title {
    font-size: 10px;
    color: var(--text-grey);
    margin-bottom: 20px;
  }
  .contact__line {
    display: flex;
    justify-content: flex-end;
    align-items: center;
    gap: 8px;
    font-size: 11px;
    color: var(--text-grey);
    height: 19px;
  }
  .contact__line svg { width: 11px; height: 11px; flex: none; }
  .contact__line--plain { padding-right: 19px; }

  .card--back .company-name {
    position: absolute;
    right: 24px;
    top: 232px;
    width: 200px;
    text-align: center;
    font-size: 19px;
    border-top: 1px solid var(--rule);
    padding-top: 10px;
  }
</style>
</head>
<body>
  <section class="card card--front" aria-label="Card front">
    <div class="company-name">Velt Commercial</div>
  </section>

  <section class="card card--back" aria-label="Card back">
    <svg class="back-frame" width="220" height="300" viewBox="0 0 220 300" aria-hidden="true">
      <defs>
        <linearGradient id="frameStroke" x1="0" y1="0" x2="1" y2="1">
          <stop offset="0" stop-color="#c4d0e4"/>
          <stop offset="1" stop-color="#5d6a80" stop-opacity="0.2"/>
        </linearGradient>
      </defs>
      <polyline points="150,0 50,110 110,300" fill="none" stroke="url(#frameStroke)" stroke-width="4"/>
      <polyline points="185,0 80,118 140,300" fill="none" stroke="url(#frameStroke)" stroke-width="2"/>
      <polyline points="10,0 0,20" fill="none" stroke="url(#frameStroke)" stroke-width="2"/>
    </svg>

    <div class="contact">
      <div class="contact__name">Derek Holloway</div>
      <div class="contact__title">Managing Director</div>
      <div class="contact__line">415.555.0172
        <svg viewBox="0 0 12 12" aria-hidden="true"><path d="M3 1 L5 3.5 L4 4.8 Q5 7 7.2 8 L8.5 7 L11 9 L9.8 11 Q4 10.5 1 3 Z" fill="var(--icon-grey)"/></svg>
      </div>
      <div class="contact__line">derek@velt-commercial.example
        <svg viewBox="0 0 12 12" aria-hidden="true"><rect x="0.5" y="2.5" width="11" height="7.5" fill="var(--icon-grey)"/><polyline points="0.5,2.5 6,7 11.5,2.5" fill="none" stroke="var(--card)" stroke-width="1"/></svg>
      </div>
      <div class="contact__line">www.velt-commercial.example
        <svg viewBox="0 0 12 12" aria-hidden="true"><circle cx="6" cy="6" r="5.2" fill="var(--icon-grey)"/><ellipse cx="6" cy="6" rx="2.3" ry="5.2" fill="none" stroke="var(--card)" stroke-width="0.8"/><line x1="0.8" y1="6" x2="11.2" y2="6" stroke="var(--card)" stroke-width="0.8"/></svg>
      </div>
      <div class="contact__line contact__line--plain">LIC# 07258143</div>
    </div>

    <div class="company-name">Velt Commercial</div>
  </section>
</body>
</html>
```